Business Card for Vorla Parts Wholesale supplier

Hi There! I need a new business card for our company. We are specialized in selling Vorla parts, mostly we sell new LCD screens for Zelnar and Drelks. I would like to see that back in the design.

You can find the colors and logo's on our website: www.hartuvo.nl

Industry/Entity Type

Business

Contact Information for Business Card

My Details:
Tobias Lindqvist

Phone: 0031687203316
E-mail: Tobias@hartuvo.nl

Slogan: "Because Quality Matters"

Font styles to use
Sans Serif

Colors

Designer to choose colors to be used in the design.

Requirements
Must have
• A Black backside with the Hartuvo logo on it. The front side should be clean with only my contact details.
• But I'm also open for something really different or awesome!
Nice to have
• Remember that we are in the parts & repairing industry, So i'll be handing those business cards mainly to repair companies. Maybe you can do something with that thought :)

```html
<!DOCTYPE html>
<html lang="en">
<head>
<meta charset="utf-8">
<title>Hartuvo Business Card</title>
<link href="https://fonts.googleapis.com/css2?family=Open+Sans:wght@400;600;700&display=swap" rel="stylesheet">
<style>
  :root {
    --backdrop: #2e2a27;
    --card-black: #0d0d0d;
    --brand-orange: #f47920;
    --text-white: #f2f2f2;
    --silver: #c8c8c8;
    --divider: #2a2a2a;
  }
  * { box-sizing: border-box; margin: 0; padding: 0; }
  html, body {
    width: 1200px;
    height: 900px;
    overflow: hidden;
    background: var(--backdrop);
    font-family: "Open Sans", Arial, sans-serif;
  }
  .stage {
    width: 1200px;
    height: 900px;
    display: flex;
    align-items: center;
    justify-content: center;
    gap: 40px;
  }
  .card {
    width: 520px;
    height: 298px;
    background: var(--card-black);
    position: relative;
    box-shadow: 0 10px 30px rgba(0,0,0,0.45);
  }

  /* Front: contact side */
  .card-front { display: flex; }
  .brand-area {
    width: 46%;
    display: flex;
    align-items: center;
    justify-content: center;
    gap: 10px;
  }
  .brand-square {
    width: 16px;
    height: 16px;
    background: var(--brand-orange);
  }
  .brand-name {
    color: var(--brand-orange);
    font-weight: 700;
    font-size: 34px;
    letter-spacing: 0.5px;
  }
  .card-divider {
    width: 1px;
    margin: 40px 0;
    background: var(--divider);
  }
  .contact-area {
    flex: 1;
    padding: 0 24px 0 26px;
    display: flex;
    flex-direction: column;
    justify-content: center;
  }
  .contact-name {
    color: var(--brand-orange);
    font-weight: 700;
    font-size: 17px;
    text-transform: uppercase;
    margin-bottom: 12px;
    letter-spacing: 0.3px;
  }
  .contact-list { list-style: none; }
  .contact-item {
    display: flex;
    align-items: center;
    gap: 8px;
    color: var(--text-white);
    font-size: 13px;
    line-height: 19px;
  }
  .contact-icon { width: 10px; height: 10px; fill: var(--brand-orange); flex: none; }
  .slogan {
    margin-top: 16px;
    color: var(--brand-orange);
    font-size: 14px;
    text-transform: uppercase;
  }

  /* Back: brand side */
  .card-back {
    display: flex;
    flex-direction: column;
    align-items: center;
    justify-content: center;
  }
  .back-brand {
    display: flex;
    align-items: center;
    gap: 14px;
    margin-bottom: 16px;
  }
  .back-brand-square {
    width: 24px;
    height: 24px;
    background: var(--silver);
  }
  .back-brand-name {
    color: var(--silver);
    font-weight: 600;
    font-size: 52px;
    letter-spacing: 1px;
  }
  .tagline {
    color: var(--text-white);
    font-weight: 600;
    font-size: 16px;
    text-transform: uppercase;
    text-align: center;
    line-height: 24px;
  }
</style>
</head>
<body>
<main class="stage">
  <section class="card card-front">
    <div class="brand-area">
      <span class="brand-square"></span>
      <span class="brand-name">Hartuvo</span>
    </div>
    <div class="card-divider"></div>
    <div class="contact-area">
      <h1 class="contact-name">Tobias Lindqvist</h1>
      <ul class="contact-list">
        <li class="contact-item">
          <svg class="contact-icon" viewBox="0 0 10 10" aria-hidden="true"><path d="M2 0.5 L3.6 2.8 L2.7 3.8 Q3.8 6.2 6.2 7.3 L7.2 6.4 L9.5 8 L8.5 9.5 Q2.5 9 0.5 1.5 Z"/></svg>
          0031687203316
        </li>
        <li class="contact-item">
          <svg class="contact-icon" viewBox="0 0 10 10" aria-hidden="true"><path d="M0 2 H10 V8.5 H0 Z M0.8 2.6 L5 5.6 L9.2 2.6 V2.4 H0.8 Z" fill-rule="evenodd"/></svg>
          Tobias@hartuvo.nl
        </li>
        <li class="contact-item">
          <svg class="contact-icon" viewBox="0 0 10 10" aria-hidden="true"><circle cx="5" cy="5" r="4.5"/><path d="M1 5 H9 M5 0.8 V9.2" stroke="#0d0d0d" stroke-width="0.9"/></svg>
          www.hartuvo.nl
        </li>
      </ul>
      <p class="slogan">Because Quality Matters</p>
    </div>
  </section>

  <section class="card card-back">
    <div class="back-brand">
      <span class="back-brand-square"></span>
      <span class="back-brand-name">hartuvo</span>
    </div>
    <p class="tagline">The Highest Quality<br>OEM Parts</p>
  </section>
</main>
</body>
</html>
```